Natural healthcare clinic needs stationery and business card design

We have had a logo developed by Pixel Harbor and are now looking at utilising it for a new business concept. The concept is a natural healthcare clinic that hosts a number of small businesses. The individual practitioners may want to utilise the host business stationery to provide a consistent message to clients.

I am looking for a stationery design - letterhead, DL brochure template and business card that uses our logo. The business name 'Bright Meadows' is all about getting rhythm back into your life so you can be fit and healthy. The stationery design should reflect this.

There are a couple of requirements for the business card, it needs to be double-sided with black and white back. There should be lines to write appointment times on. The cards may need to be custom named on the front for example Carol Fenwick, Remedial Therapist and Aromatherapist. Therefore if a template can be provided so we can customise this information using MS Publisher, it would be appreciated.

The DL brochure template needs to be A4 folded to DL. I am looking for a consistent brand message that can be utilised to produce our own clinic brochures.

The natural healthcare clinic will host the following types of businesses - remedial massage, pregnancy massage, oncology massage, aromatherapy, acupuncture - as a bit of a guide.

Target Market(s)

25-45 year old male and females who work full time.

Industry/Entity Type

Healthcare

Requirements
Must have
• Use the logo I have already.

```html
<!DOCTYPE html>
<html lang="en">
<head>
<meta charset="utf-8">
<title>Bright Meadows Stationery</title>
<link href="https://fonts.googleapis.com/css2?family=Source+Sans+3:wght@400;600&display=swap" rel="stylesheet">
<style>
  :root {
    --backdrop: #d8d4cd;
    --paper: #ffffff;
    --paper-shade: #eeeeee;
    --leaf-dark: #2f6e2c;
    --leaf-mid: #5f9a43;
    --leaf-light: #8fbf6a;
    --brand-olive: #6d6a2c;
    --ink: #3a3a3a;
    --ink-soft: #777777;
    --rule: #4f8a3c;
  }
  * { box-sizing: border-box; margin: 0; padding: 0; }
  html, body { width: 1200px; height: 811px; overflow: hidden; }
  body {
    background: var(--backdrop);
    font-family: "Source Sans 3", "Helvetica Neue", Arial, sans-serif;
    color: var(--ink);
    position: relative;
  }
  .sheet {
    position: absolute;
    background: var(--paper);
    box-shadow: 0 3px 10px rgba(0,0,0,0.18);
    overflow: hidden;
  }
  .swoosh { position: absolute; left: 0; bottom: 0; width: 100%; }
  .brand {
    position: absolute;
    z-index: 2;
    display: flex;
    align-items: center;
    gap: 0.3em;
    color: var(--brand-olive);
    font-weight: 400;
    white-space: nowrap;
    line-height: 1;
  }
  .brand-dot {
    width: 0.7em; height: 0.7em;
    border-radius: 50%;
    background: var(--leaf-mid);
    flex: none;
  }

  /* Letterhead */
  .letterhead { left: 271px; top: 102px; width: 303px; height: 418px; }
  .letterhead-header {
    position: absolute; left: 162px; top: 22px;
    display: flex; gap: 10px;
    font-size: 4px; line-height: 1.3; color: var(--ink-soft);
  }
  .letterhead-header .name { color: var(--leaf-dark); font-weight: 600; font-size: 4.5px; }
  .letterhead-header .divider { width: 1px; background: var(--ink-soft); height: 22px; }
  .letterhead-rule {
    position: absolute; left: 18px; right: 18px; top: 46px;
    height: 1px; background: var(--rule);
  }
  .letter-body {
    position: absolute; left: 25px; top: 92px; width: 255px;
    font-size: 5.2px; line-height: 1.4; color: var(--ink);
  }
  .letter-body p { margin-bottom: 6px; }
  .letterhead .brand { right: 40px; bottom: 68px; font-size: 9px; }

  /* Folder cover */
  .cover { left: 615px; top: 83px; width: 349px; height: 442px; }
  .cover .brand { left: 107px; top: 258px; font-size: 20px; }

  /* Business cards */
  .card { width: 135px; height: 77px; left: 166px; }
  .card-front { top: 555px; }
  .card-front .brand { left: 22px; top: 40px; font-size: 11px; }
  .card-back { top: 651px; height: 75px; }
  .card-back .contact {
    position: absolute; left: 13px; top: 13px;
    font-size: 3.8px; line-height: 1.35; color: var(--ink-soft);
  }
  .card-back .contact .name { font-size: 6.5px; color: var(--ink); }
  .card-back .contact .role { font-size: 4px; margin-bottom: 4px; }
  .card-back .divider {
    position: absolute; left: 70px; top: 12px; width: 1px; height: 36px;
    background: var(--ink-soft);
  }
  .card-back .brand { left: 77px; top: 40px; font-size: 6.5px; }

  /* Envelopes */
  .envelope-front { left: 333px; top: 563px; width: 332px; height: 161px; }
  .envelope-front .brand { left: 236px; top: 104px; font-size: 8px; }
  .envelope-back { left: 693px; top: 562px; width: 332px; height: 162px; background: #f4f4f4; }
  .envelope-flap { position: absolute; left: 0; top: 0; width: 100%; height: 46px; }
  .envelope-back .brand { left: 130px; top: 28px; font-size: 8px; }
</style>
</head>
<body>

  <section class="sheet letterhead">
    <div class="letterhead-header">
      <div>
        <div class="name">Your Name</div>
        <div>Position</div>
        <div>Address xxxxxxxxxxxxxxxx</div>
        <div>Phone xxxxxxxxxxxxxxxx</div>
      </div>
      <div class="divider"></div>
      <div>
        <div>&nbsp;</div>
        <div>Fax xxxxxxxxxxxxxxxx</div>
        <div>Email xxxxxxxxxxxxxxxx</div>
      </div>
    </div>
    <div class="letterhead-rule"></div>
    <div class="letter-body">
      <p>1800, Elm Hollow Road<br>Fairhaven, CA 90000.</p>
      <p>January 29th, 2011</p>
      <p>Mr. Aldwick<br>President, Aldwick Family Centre<br>52 Orchard Way<br>Northgate, NY 10000</p>
      <p>Dear Mr. Aldwick:</p>
      <p>In the first paragraph, one needs to give a brief introduction of oneself. One should also give reference to the purpose of the letter in brief.<br>
      The second paragraph needs to give the details of the letter and its need. This paragraph is mostly longer than the others and plays the main role in the letter. Keep the sentences short and to the point. Avoid using complex words and sentences.</p>
      <p style="margin-top:12px">The third and last paragraph is the conclusion of the letter and can be kept short.</p>
      <p>Sincerely,</p>
      <p>(this is where the signature of the writer will be placed)</p>
      <p>Dana Whitlow<br>Read more at Letterwise: http://www.letterwise.example/articles/letter-format-guide.html</p>
    </div>
    <div class="brand"><span class="brand-dot"></span>Bright Meadows</div>
    <svg class="swoosh" viewBox="0 0 300 60" preserveAspectRatio="none" height="62" aria-hidden="true">
      <path d="M0,40 C80,30 180,46 300,0 L300,12 C190,54 90,43 0,43 Z" fill="var(--leaf-dark)"/>
      <path d="M60,52 C150,44 230,52 300,30 L300,38 C230,58 150,54 60,54 Z" fill="var(--leaf-mid)"/>
      <path d="M150,60 C210,56 260,48 300,36 L300,60 Z" fill="var(--leaf-light)"/>
    </svg>
  </section>

  <section class="sheet cover">
    <div class="brand"><span class="brand-dot"></span>Bright Meadows</div>
    <svg class="swoosh" viewBox="0 0 300 60" preserveAspectRatio="none" height="70" aria-hidden="true">
      <path d="M0,40 C80,30 180,46 300,0 L300,12 C190,54 90,43 0,43 Z" fill="var(--leaf-dark)"/>
      <path d="M60,52 C150,44 230,52 300,30 L300,38 C230,58 150,54 60,54 Z" fill="var(--leaf-mid)"/>
      <path d="M150,60 C210,56 260,48 300,36 L300,60 Z" fill="var(--leaf-light)"/>
    </svg>
  </section>

  <section class="sheet card card-front">
    <div class="brand"><span class="brand-dot"></span>Bright Meadows</div>
    <svg class="swoosh" viewBox="0 0 300 60" preserveAspectRatio="none" height="22" aria-hidden="true">
      <path d="M0,40 C80,30 180,46 300,0 L300,12 C190,54 90,43 0,43 Z" fill="var(--leaf-dark)"/>
      <path d="M60,52 C150,44 230,52 300,30 L300,38 C230,58 150,54 60,54 Z" fill="var(--leaf-mid)"/>
      <path d="M150,60 C210,56 260,48 300,36 L300,60 Z" fill="var(--leaf-light)"/>
    </svg>
  </section>

  <section class="sheet card card-back">
    <div class="contact">
      <div class="name">Your Name</div>
      <div class="role">Position</div>
      <div>Address: xxxxxxxxxxxxxx</div>
      <div>Phone: xxxxxxxxxxxxxx</div>
      <div>Fax: xxxxxxxxxxxxxx</div>
      <div>Email: xxxxxxxxxxxxxx</div>
    </div>
    <div class="divider"></div>
    <div class="brand"><span class="brand-dot"></span>Bright Meadows</div>
    <svg class="swoosh" viewBox="0 0 300 60" preserveAspectRatio="none" height="18" aria-hidden="true">
      <path d="M0,40 C80,30 180,46 300,0 L300,12 C190,54 90,43 0,43 Z" fill="var(--leaf-dark)"/>
      <path d="M60,52 C150,44 230,52 300,30 L300,38 C230,58 150,54 60,54 Z" fill="var(--leaf-mid)"/>
      <path d="M150,60 C210,56 260,48 300,36 L300,60 Z" fill="var(--leaf-light)"/>
    </svg>
  </section>

  <section class="sheet envelope-front">
    <div class="brand"><span class="brand-dot"></span>Bright Meadows</div>
    <svg class="swoosh" viewBox="0 0 300 60" preserveAspectRatio="none" height="40" aria-hidden="true">
      <path d="M100,48 C170,42 230,44 300,0 L300,10 C230,54 170,50 100,50 Z" fill="var(--leaf-dark)"/>
      <path d="M150,56 C210,50 260,46 300,26 L300,34 C260,56 210,58 150,58 Z" fill="var(--leaf-mid)"/>
      <path d="M200,60 C240,58 275,52 300,40 L300,60 Z" fill="var(--leaf-light)"/>
    </svg>
  </section>

  <section class="sheet envelope-back">
    <svg class="envelope-flap" viewBox="0 0 332 46" preserveAspectRatio="none" aria-hidden="true">
      <path d="M0,0 L332,0 L318,44 L14,44 Z" fill="var(--paper)"/>
      <path d="M14,44 L318,44" stroke="var(--paper-shade)" stroke-width="2"/>
    </svg>
    <div class="brand"><span class="brand-dot"></span>Bright Meadows</div>
  </section>

</body>
</html>
```